Vibrant, yet professional, stationery set and other designs required.

I need to source a fantastic designer for a new project as part of my company using a new logo designed via sketch harbor.

**UPDATE** I am not looking for just 'fine' design that will suffice. I am looking for something great.

We are a life assurance brokerage based in Dublin, Ireland and BrightRoost.ie is our new website aimed at providing services for young families in Ireland. We are hoping to be the 'Velro' level of service providers in this area and I am looking for the quality of design to reflect this :-) Hopefully that makes sense!

I have a preference for straight lines over curves and waves.

I need...

1. Business card
2. Letterhead
3. Banner (for printing - 76cm X 305cm)
4. Car branding for KORVA 9 (2014 sport model) I believe the templates are freely available online.

Target Market(s)

Parents in Ireland - Aged 27 to 50.

Industry/Entity Type

Financial Planning

Colors

Designer to choose colors to be used in the design.

Requirements
Must have
• All of the items listed in the description above. I like clean, bright, legible, vibrant and professional design.
Should not have
• No silly or 'cheap' looking designs. This is a professional company looking to provide a professional service.

```html
<!DOCTYPE html>
<html lang="en">
<head>
<meta charset="utf-8">
<title>BrightRoost.ie – Business Card</title>
<link rel="stylesheet" href="https://fonts.googleapis.com/css2?family=Oswald:wght@500&family=Roboto:wght@400;500&display=swap">
<style>
  :root {
    --stage: #d9d9d9;
    --card-dark: #1c1c1d;
    --card-light: #f7f7f6;
    --logo-grey: #a9adaf;
    --accent: #f07f13;
    --ink: #4a4a4a;
    --ink-soft: #5e5e5e;
    --rule: #b8b8b8;
    --white: #ffffff;
  }
  * { box-sizing: border-box; margin: 0; padding: 0; }
  html, body { width: 1200px; height: 900px; overflow: hidden; }
  body {
    background: var(--stage);
    font-family: "Roboto", Arial, sans-serif;
    display: flex;
    flex-direction: column;
    align-items: center;
    justify-content: center;
    gap: 44px;
  }
  .card {
    width: 640px;
    height: 366px;
    position: relative;
    box-shadow: 0 6px 18px rgba(0,0,0,.18);
  }

  /* Front */
  .card--front {
    background: var(--card-dark);
    display: flex;
    flex-direction: column;
    align-items: center;
    justify-content: center;
  }
  .brand {
    display: flex;
    align-items: center;
    gap: 14px;
  }
  .brand__dot {
    width: 22px; height: 22px;
    border-radius: 50%;
    background: var(--accent);
  }
  .brand__name {
    font-family: "Roboto", Arial, sans-serif;
    font-weight: 500;
    font-size: 58px;
    color: var(--logo-grey);
    letter-spacing: -0.5px;
  }
  .front__web {
    margin-top: 30px;
    color: var(--white);
    font-size: 14px;
    letter-spacing: 7px;
  }

  /* Back */
  .card--back {
    background: var(--card-light);
  }
  .identity {
    position: absolute;
    right: 365px;
    top: 112px;
    text-align: right;
  }
  .identity__name {
    font-family: "Oswald", "Arial Narrow", sans-serif;
    font-weight: 500;
    font-size: 34px;
    color: var(--accent);
    letter-spacing: 0.5px;
    line-height: 1.05;
  }
  .identity__role {
    font-size: 16px;
    font-weight: 500;
    color: var(--ink-soft);
    margin-top: 6px;
  }
  .divider {
    position: absolute;
    left: 293px;
    top: 96px;
    width: 1px;
    height: 120px;
    background: linear-gradient(to bottom, transparent, var(--rule) 15%, var(--rule) 85%, transparent);
  }
  .contacts {
    position: absolute;
    left: 310px;
    top: 98px;
    list-style: none;
  }
  .contacts li {
    display: flex;
    align-items: center;
    gap: 9px;
    font-size: 16px;
    color: var(--ink);
    line-height: 23px;
  }
  .icon { width: 14px; height: 14px; fill: var(--accent); flex: none; }
  .address {
    position: absolute;
    left: 90px;
    bottom: 58px;
    display: flex;
    align-items: center;
    gap: 10px;
    font-size: 17px;
    color: var(--ink);
  }
  .address .icon { width: 15px; height: 18px; }
</style>
</head>
<body>

  <section class="card card--front">
    <div class="brand">
      <span class="brand__dot"></span>
      <span class="brand__name">BrightRoost.ie</span>
    </div>
    <p class="front__web">www.brightroost.ie</p>
  </section>

  <section class="card card--back">
    <div class="identity">
      <h1 class="identity__name">LIAM CARTER</h1>
      <p class="identity__role">CEO/FOUNDER</p>
    </div>
    <div class="divider"></div>
    <ul class="contacts">
      <li>
        <svg class="icon" viewBox="0 0 14 14"><path d="M3 1l2.2 2.6-1.3 1.6c.9 1.9 2.3 3.3 4.2 4.2l1.6-1.3L12.3 10l-1 2.6C6 12.6 1.4 8 1.4 2.8z"/></svg>
        614 207 3391
      </li>
      <li>
        <svg class="icon" viewBox="0 0 14 14"><path d="M4 0h6a1 1 0 011 1v12a1 1 0 01-1 1H4a1 1 0 01-1-1V1a1 1 0 011-1zm.6 1.6v9.4h4.8V1.6zM7 11.6a.8.8 0 100 1.6.8.8 0 000-1.6z"/></svg>
        872 519 4406
      </li>
      <li>
        <svg class="icon" viewBox="0 0 14 14"><path d="M3.5 1h7v3h-7zM1 5h12v6h-2.5v2h-7v-2H1zm3.5 4v3h5V9z"/></svg>
        453 760 2185
      </li>
      <li>
        <svg class="icon" viewBox="0 0 14 14"><path d="M1 3h12v8H1zm1 1.2v.3l5 3.3 5-3.3v-.3z"/></svg>
        hello@brightroost.ie
      </li>
      <li>
        <svg class="icon" viewBox="0 0 14 14"><circle cx="7" cy="7" r="6.2"/><path d="M1 7h12M7 1c2 2 2 10 0 12M7 1c-2 2-2 10 0 12" stroke="#f7f7f6" stroke-width="1" fill="none"/></svg>
        www.brightroost.ie
      </li>
    </ul>
    <p class="address">
      <svg class="icon" viewBox="0 0 15 18"><path d="M7.5 0A6 6 0 001.5 6c0 4.5 6 12 6 12s6-7.5 6-12a6 6 0 00-6-6zm0 3.4a2.6 2.6 0 110 5.2 2.6 2.6 0 010-5.2z"/></svg>
      14 Harbour Row, Ringsend, Dublin D04 K7X2
    </p>
  </section>

</body>
</html>
```